RW Framewell Inc Business cards

We need business cards using our existing logo but slightly modified. Right now the logo says RW Loadbearing Masonry. We want to keep the RW part of the design, but replace the Structural Concrete portion with "FRAMEWELL". Please see the attached file.
Ideally this would be a blank template so we can add Different Names, titles, and phone numbers later.
On the one side we want only the logo and on the other side the detail. I'm attaching an example for you to see.
Please reach out with any other questions. Our address and other details will be given out once we find a design we like.

Target Market(s)

Construction Industry

```html
<!DOCTYPE html>
<html lang="en">
<head>
<meta charset="utf-8">
<title>RW Framewell Inc Business Cards</title>
<link href="https://fonts.googleapis.com/css2?family=Roboto:wght@400;500;700&display=swap" rel="stylesheet">
<style>
  :root {
    --backdrop: #c9c9c9;
    --card: #fbfbfb;
    --brand-blue: #2f63ad;
    --brand-gray: #6b6b6b;
    --text-gray: #707070;
    --shadow: rgba(0, 0, 0, 0.22);
  }
  * { margin: 0; padding: 0; box-sizing: border-box; }
  html, body {
    width: 1200px;
    height: 852px;
    overflow: hidden;
    background: var(--backdrop);
    font-family: "Roboto", Arial, sans-serif;
  }
  .stage { position: relative; width: 1200px; height: 852px; }

  .card {
    position: absolute;
    width: 490px;
    height: 280px;
    background: var(--card);
    border-radius: 22px;
    overflow: hidden;
    box-shadow: 0 8px 18px var(--shadow);
  }

  /* Front: logo only */
  .card-front { left: 90px; top: 140px; }
  .card-front .wordmark {
    position: absolute;
    left: 0; right: 0; top: 82px;
    text-align: center;
    color: var(--brand-blue);
    font-weight: 700;
    line-height: 1;
  }
  .wordmark .initials { display: block; font-size: 78px; letter-spacing: 2px; }
  .wordmark .name { display: block; font-size: 24px; letter-spacing: 6px; margin-top: 6px; }
  .edge-band {
    position: absolute;
    left: 0; right: 0; bottom: 0;
    height: 12px;
    display: flex;
  }
  .edge-band .gray { width: 46%; background: var(--brand-gray); }
  .edge-band .blue { flex: 1; background: var(--brand-blue); }

  /* Back: details */
  .card-back { left: 620px; top: 440px; }
  .card-back .wordmark {
    position: absolute;
    right: 34px; top: 34px;
    text-align: right;
    color: var(--brand-blue);
    font-weight: 700;
    line-height: 1;
  }
  .card-back .wordmark .initials { font-size: 54px; }
  .card-back .wordmark .name { font-size: 17px; letter-spacing: 4px; margin-top: 4px; }

  .person { position: absolute; left: 34px; top: 62px; }
  .person .full-name { color: var(--brand-blue); font-size: 20px; font-weight: 700; }
  .person .role { color: var(--text-gray); font-size: 13px; margin-top: 3px; }

  .contact-list {
    position: absolute;
    left: 34px; bottom: 30px;
    list-style: none;
    color: var(--text-gray);
    font-size: 13px;
    line-height: 1.45;
  }
  .contact-list li { display: flex; align-items: flex-start; gap: 8px; }
  .contact-list svg { width: 12px; height: 12px; margin-top: 3px; flex: none; fill: var(--brand-blue); }
  .contact-list .no-icon { padding-left: 20px; }

  .web-tab {
    position: absolute;
    right: 0; bottom: 0;
    width: 225px; height: 56px;
    background: var(--brand-blue);
    border-top-left-radius: 22px;
    color: #fff;
    font-size: 13px;
    font-weight: 700;
    display: flex;
    align-items: center;
    justify-content: center;
  }
</style>
</head>
<body>
<main class="stage">
  <section class="card card-front" aria-label="Business card front">
    <div class="wordmark">
      <span class="initials">RW</span>
      <span class="name">FRAMEWELL</span>
    </div>
    <div class="edge-band"><span class="gray"></span><span class="blue"></span></div>
  </section>

  <section class="card card-back" aria-label="Business card back">
    <div class="wordmark">
      <span class="initials">RW</span>
      <span class="name">FRAMEWELL</span>
    </div>
    <div class="person">
      <p class="full-name">Alan RW Porter</p>
      <p class="role">Managing Director</p>
    </div>
    <ul class="contact-list">
      <li>
        <svg viewBox="0 0 24 24" aria-hidden="true"><path d="M6.6 10.8a15 15 0 0 0 6.6 6.6l2.2-2.2a1 1 0 0 1 1-.25 11.4 11.4 0 0 0 3.6.57 1 1 0 0 1 1 1V20a1 1 0 0 1-1 1A17 17 0 0 1 3 4a1 1 0 0 1 1-1h3.5a1 1 0 0 1 1 1c0 1.25.2 2.45.57 3.57a1 1 0 0 1-.25 1z"/></svg>
        <span>555-010-2040</span>
      </li>
      <li>
        <svg viewBox="0 0 24 24" aria-hidden="true"><path d="M2 5h20v14H2z M2 5l10 8 10-8" fill="none" stroke="#2f63ad" stroke-width="2.4"/></svg>
        <span>alan@framewellinc.com</span>
      </li>
      <li class="no-icon">78 Girder Lane, Millbrook,</li>
      <li class="no-icon">Oregon, US 970412</li>
    </ul>
    <div class="web-tab">www.framewellinc.com</div>
  </section>
</main>
</body>
</html>
```